Dentistry Office

We want a new design for a Dentist's office website.

The theme is: "We provide high quality, state-of-the-art, dental care in a comfortable, caring environment."

The site currently has a menu on the left of the page with about 40 items on it. There is a great deal of textual content on each page, plus several illustrations.

We want to do this using CSS, so we need specifications in the CSS for all possible elements. The CSS needs to be named in a logical manner for easy use.

Every dentist on the planet seems to use lots of Flash. We don't want to because it is so distracting. We are looking for an elegant solution targeting 24-55 age group, but not excluding anyone.

The following (from another dentist's site) can give you a taste of what we want to communicate on the site:

"After 20 years of teaching dentists how to refine their technique and many years of writing textbooks, I currently devote my time to my office and the hands-on practice of dentistry. I'd like to welcome you personally to my dental practice, and I invite you to meet my highly experienced team of professionals.

"We have offered complete dental care of the highest quality since 1978. We provide Preventive Services, Tooth Whitening and Cosmetic Dentistry for a beautiful smile, Endodontics (root canal treatment) to treat painful teeth, Sedation Dentistry so you can relax, and Dental Implants to restore what is missing. We offer total care.

"Our approach to your health is simple: We use our education, experience and dedication to provide every patient with superior dental care.

"This passion for excellence is not just a goal, but a standard every member of our team holds.

"We also pride ourselves with our state of the art procedures, training and technology. This includes creating a beautiful smile using techniques that preserve as much of the original tooth as possible.

"Our abilities are renowned throughout the dental profession and I hope if you have any questions you will contact us by an e-mail note, by phone or just by dropping by."

Keep in mind the screen shape and dimensions. Your design needs to work in the normal screen proportions, regardless of how it looks when you post it here. Scrolling is OK, but the first impression needs to work.
Updates

Keep in mind that there will be about 250 words, or more, on each page.

Competitors web sites:

http://www.brindlecovedentist.example/

http://www.brindlecovedentalcare.example/

http://www.grinsbymarlowvaledental.example/

http://www.tenbyfamilydentalcare.example/

http://www.quelmardental.example/

http://www.dovrinadental.example/

We need to compete with these.

Target Market(s)

Generally adults seeking the most experienced and comfortable-to-be-with dentist.

Industry/Entity Type

Training

Requirements
Must have
• Must stand apart from other dentists.
• Must be elegant.
• Must have a horizontal menu structure across all columns, NOT a vertical that requires scrolling, no popout, pop down, etc. menus.
• We are looking for something special.
• Do not waste your time or ours putting up templates and things you have used before.
• Personally, I do not see how someone outside the US can understand the northern California dental market. But you are welcome to try.
Should not have
• Flash or graphics that move
• The look of a template
• Folksy fonts
• Looks like you used it 20 times before

```html
<!DOCTYPE html>
<html lang="en">
<head>
<meta charset="utf-8">
<title>Henry Aldren, DDS, FAGD – Alderbrook Dentist</title>
<link rel="stylesheet" href="https://fonts.googleapis.com/css2?family=Gelasio:ital,wght@0,400;0,700;1,400;1,700&family=Arimo:wght@400;700&display=swap">
<style>
:root{
  --ink:#222;
  --ink-soft:#444;
  --brand-blue:#2f6db0;
  --heading:#2b4868;
  --nav-top:#3a3a3a;
  --nav-bottom:#050505;
  --panel:#dde5ee;
  --panel-line:#9fb0c2;
  --page-top:#c9d1d8;
  --page-bottom:#6a7d8c;
  --footer:#5d7182;
  --hero-a:#b9c6d6;
  --hero-b:#7f94ad;
  --hero-edge:#51657d;
  --white:#fff;
}
*{margin:0;padding:0;box-sizing:border-box}
html,body{width:852px;height:1200px;overflow:hidden}
body{background:linear-gradient(180deg,var(--page-top) 0,#aeb9c3 600px,var(--page-bottom) 1070px,var(--footer) 1200px);font-family:Arimo,Arial,sans-serif;color:var(--ink);position:relative}

.site-header{position:absolute;left:36px;top:0;width:780px;height:73px;background:linear-gradient(180deg,#fff,#eef1f4)}
.brand{position:absolute;left:25px;top:22px;font-family:Gelasio,Georgia,serif;font-size:25px;color:var(--ink);line-height:1}
.brand span{color:var(--brand-blue)}
.brand-sub{position:absolute;left:155px;top:50px;font-family:Gelasio,Georgia,serif;font-size:12.5px}
.header-address{position:absolute;left:654px;top:17px;font-family:Gelasio,Georgia,serif;font-size:10px;line-height:12.5px;font-style:normal}

.main-nav{position:absolute;left:36px;top:73px;width:780px;height:30px;background:linear-gradient(180deg,var(--nav-top),var(--nav-bottom));display:flex;align-items:center;justify-content:space-around;padding:0 12px}
.main-nav a{color:var(--white);text-decoration:none;font-family:Gelasio,Georgia,serif;font-weight:700;font-size:11.5px}
.main-nav .divider{width:1px;height:16px;background:#bbb}

.hero{position:absolute;left:36px;top:107px;width:778px;height:190px;background:linear-gradient(100deg,#c8d2de 0,var(--hero-a) 35%,var(--hero-b) 100%);border-bottom:4px solid var(--hero-edge)}
.hero-photo{position:absolute;right:0;top:0;width:150px;height:186px;background:linear-gradient(160deg,#e9ddd3,#c8a996 60%,#d27fa0)}
.hero-quote{position:absolute;left:37px;top:56px;width:390px;font-family:Gelasio,Georgia,serif;font-size:16.5px;line-height:22px;color:var(--white)}
.hero-mark{position:absolute;font-family:Gelasio,Georgia,serif;font-size:28px;color:#e8eef5;opacity:.8}

.topic-menu{position:absolute;left:36px;top:307px;width:780px;height:150px;background:var(--panel);display:flex;padding:6px 0 0 27px}
.topic-col{width:168px}
.topic-col:nth-child(3){width:165px}
.topic-col:nth-child(4){width:144px}
.topic-col h3{font-family:Gelasio,Georgia,serif;font-weight:400;font-size:13px;border-bottom:1px solid var(--panel-line);width:112px;padding-bottom:1px;margin-bottom:3px}
.topic-col ul{list-style:none}
.topic-col li{font-size:9.5px;line-height:12.2px;color:var(--ink-soft)}
.topic-col li::before{content:"› ";font-weight:700;color:#555}

.content{position:absolute;left:36px;top:460px;width:780px;height:607px;background:var(--white)}
.article{position:absolute;left:27px;top:12px;width:520px;font-size:9.3px;line-height:11.5px;color:var(--ink-soft)}
.article h1,.article h2{font-family:Gelasio,Georgia,serif;font-weight:400;color:var(--heading)}
.article h1{font-size:17px;line-height:20px;margin-bottom:6px}
.article h2{font-size:13px;line-height:16px;margin:10px 0 5px}
.article p{margin-bottom:7px}
.services{list-style:none}
.services li{line-height:16.5px}
.services li::before{content:"›";font-weight:700;margin-right:6px}
.article .approach{font-family:Gelasio,Georgia,serif;font-size:12px;line-height:15.5px;color:var(--heading);width:540px;margin:10px 0 10px}
.article .approach-last{margin-bottom:26px}
.article .signature{font-family:Gelasio,Georgia,serif;font-size:12.5px;line-height:15px;color:var(--heading);margin-bottom:0}

.office-photo{position:absolute;left:576px;top:36px;width:165px;height:121px;background:linear-gradient(180deg,#a9b58f,#6b6248 55%,#8a8f6e);border:3px solid #e5e5e5;box-shadow:0 0 2px #999}
.sidebox{position:absolute;left:576px;width:200px;border:1px solid #9aa5b0;border-radius:9px;background:linear-gradient(180deg,#fff,#f1f3f5);box-shadow:0 1px 3px rgba(0,0,0,.25)}
.sidebox h4{font-family:Gelasio,Georgia,serif;font-weight:400;font-size:13.5px;text-align:center;margin-top:6px}
.map-box{top:183px;height:264px}
.map-area{margin:8px auto 0;width:180px;height:205px;background:linear-gradient(135deg,#f4f6f8,#dfe5ec);border:1px solid #c4ccd4}
.map-link{display:block;text-align:center;font-size:9px;text-decoration:underline;color:var(--ink);margin-top:8px}
.hours-box{top:455px;height:127px}
.hours-box p{font-size:10px;margin:4px 0 4px 16px}
.hours-box ul{list-style:none;margin-left:16px}
.hours-box li{font-size:10px;font-weight:700;font-style:italic;line-height:13px;border-bottom:1px solid #ddd;width:150px}
.hours-box li::before{content:"› ";font-style:normal}

.site-footer{position:absolute;left:36px;top:1096px;color:var(--white);font-size:9px;font-weight:700;line-height:11px}
.site-footer .gap{height:14px}
.link-box{position:absolute;left:477px;top:1087px;width:331px;height:104px;background:#f3f4f5;border-radius:8px;border:1px solid #a0aab4}
.link-box h5{font-size:9.5px;font-weight:400;position:absolute;left:10px;top:8px}
.link-col{position:absolute;top:25px;width:100px}
.link-col .badge{width:60px;height:24px;background:#4d6a3e;margin-bottom:4px}
.link-col:nth-child(3) .badge{background:#8a8f98}
.link-col:nth-child(4) .badge{width:80px;background:#3e6f72}
.link-col ul{list-style:none}
.link-col li{font-size:8.5px;line-height:9.6px}
</style>
</head>
<body>

<header class="site-header">
  <div class="brand">Henry Aldren, <span>DDS, FAGD</span></div>
  <div class="brand-sub">Alderbrook Dentist</div>
  <address class="header-address">Henry Aldren, DDS, FAGD<br>1420 Larkfield Ave. Ste E<br>Alderbrook, CA 95000<br>555-014-1190</address>
</header>

<nav class="main-nav">
  <a href="#">Home</a><span class="divider"></span>
  <a href="#">Why We Are Different?</a><span class="divider"></span>
  <a href="#">Technologies We Offer</a><span class="divider"></span>
  <a href="#">Meet Dr. Aldren</a><span class="divider"></span>
  <a href="#">Our Staff</a><span class="divider"></span>
  <a href="#">Contact Us / Links</a>
</nav>

<section class="hero">
  <span class="hero-mark" style="left:26px;top:36px">“</span>
  <p class="hero-quote">Alderbrook Dentist - Henry Aldren, DDS, Providing Cosmetic Dentistry Excellence to Patients in Alderbrook, Alder County and the Northern Bay Area.</p>
  <span class="hero-mark" style="left:392px;top:128px">”</span>
  <div class="hero-photo" role="img" aria-label="Portrait of a smiling patient holding a pink daisy"></div>
</section>

<section class="topic-menu">
  <div class="topic-col"><h3>Education</h3><ul>
    <li>Emergency Dental Care</li><li>Your Mouth</li><li>Your Tooth</li><li>Cracked Tooth?</li><li>Missing a Tooth?</li><li>Sensitive Teeth</li><li>Dry Mouth</li><li>Tooth Grinding</li><li>Sleep Dentistry</li><li>Videos</li></ul></div>
  <div class="topic-col"><h3>Preventative</h3><ul>
    <li>What is Preventive Care?</li><li>Taking Care of Your Teeth</li><li>Eating Right</li><li>Dental Check-Ups</li><li>Sealants</li><li>Periodontal Disease</li><li>Kicking the Habit</li><li>Night Guards</li><li>Dental X-Rays</li><li>Antibiotics with Treatment</li></ul></div>
  <div class="topic-col"><h3>Cosmetics</h3><ul>
    <li>Cosmetic Dentistry</li><li>Bleaching and Whitening</li><li>Cosmetic Bonding</li><li>Esthetic Veneers</li><li>Tooth Shaping</li></ul></div>
  <div class="topic-col"><h3>Restorations</h3><ul>
    <li>Crowns/Caps: Each Step</li><li>CMBRs</li><li>Porcelain Bridges</li><li>Bonded Dental Bridges</li><li>Gold Restorations</li><li>Implants</li><li>Treating Cracked Teeth</li><li>Periodontal (gum) Treatment</li></ul></div>
  <div class="topic-col"><h3>Visiting our office</h3><ul>
    <li>Where to Stay</li><li>First Visit / Map</li><li>Financial Policy</li><li>Dental Insurance</li></ul></div>
</section>

<main class="content">
  <article class="article">
    <h1>Welcome to Our Website</h1>
    <p>In Alderbrook, when you’re a patient of Dr. Aldren, you can be confident that you’re receiving care from the most experienced, knowledgeable, and skilled cosmetic dentist in Alder County.</p>
    <p>Dr. Aldren is an award-winning leader in restorative dentistry and a genial professional. His humor, dedication, and talent ensure you a pleasant experience and superb, long-lasting results.</p>
    <h2>Dr. Aldren Provides</h2>
    <ul class="services">
      <li>General dentistry—oral hygiene, cavity detection and repair, crowns.</li>
      <li>Cosmetic/restorative dentistry—broken or misshapen teeth, crooked smiles, unsightly gaps</li>
      <li>Non-metal fillings—nontoxic, durable tooth-colored resin fillings that are proven to provide better results</li>
      <li>Tooth shaping—extending, shortening or otherwise reshaping teeth for improved esthetics</li>
      <li>Complete smile make-over’s—resin veneers that reshape the whole mouth while preserving natural teeth</li>
      <li>Tooth whitening—at-home bleaching options to make teeth appear years younger</li>
      <li>Laser Dentistry, Sleep Dentistry, and Implant Dentistry with the Finest and Latest Equipment and Materials.</li>
      <li>Dental Implants to replace missing teeth.</li>
      <li>Sedation Dentistry so you can be relaxed.</li>
    </ul>
    <h2>Dr. Aldren’ Commitment</h2>
    <p>After 25 years of teaching dentists how to refine their technique and many years of writing textbooks,<br>I currently devote my time to my office and the hands-on practice of dentistry. I’d like to welcome you personally to my dental practice, and I invite you to meet my highly experienced team of professionals.</p>
    <p>Dr. Aldren and his Associated have offered complete dental care of the highest quality since 1978. We provide Preventive Services, Tooth Whitening and Cosmetic Dentistry for a beautiful smile, Endodontics (root canal treatment) to treat painful teeth, Sedation Dentistry so you can relax, and Dental Implants to restore what is missing. We offer total care.</p>
    <p class="approach">Our approach to your health is simple: We use our education, experience and dedication to provide every patient with superior dental care.</p>
    <p class="approach approach-last">This passion for excellence is not just a goal, but a standard every member of our team holds.</p>
    <p>We also pride ourselves with our state of the art procedures, training and technology. This includes creating a beautiful smile using techniques that preserve as much of the original tooth as possible.</p>
    <p>Our abilities are renowned throughout the dental profession and I hope if you have any questions you will contact us by an e-mail note, by phone or just by dropping by.</p>
    <p>Thank you.</p>
    <p>Sincerely,</p>
    <p class="signature">Henry Aldren, DDS FAGD</p>
  </article>

  <div class="office-photo" role="img" aria-label="Photo of the dental office building among trees"></div>

  <aside class="sidebox map-box">
    <h4>Alderbrook Map:</h4>
    <div class="map-area" role="img" aria-label="Street map showing the route to the office"></div>
    <a class="map-link" href="#">Click for Large View</a>
  </aside>

  <aside class="sidebox hours-box">
    <h4>Office Timing</h4>
    <p>Our usual office hours are:</p>
    <ul>
      <li>Monday 9 am to 6 pm</li>
      <li>Tuesday 9 am to 5 pm</li>
      <li>Wednesday 9 am to 5 pm</li>
      <li>Thursday 9 am to 5 pm</li>
      <li>Friday 7:30 am to 5 pm</li>
    </ul>
  </aside>
</main>

<footer class="site-footer">
  Copyright © 2010 draldren.example. All Rights Reserved.
  <div class="gap"></div>
  Office Phone: (555) 014-1190<br>
  Office Fax: (555) 014-4033<br>
  email Dr. Aldren at: draldren@draldren.example
</footer>

<div class="link-box">
  <h5>Dental Links:</h5>
  <div class="link-col" style="left:10px"><div class="badge"></div><ul>
    <li>Emergency Dental Help</li><li>Oral Health Videos</li><li>Oral Health Topics</li><li>Dental Minute News</li></ul></div>
  <div class="link-col" style="left:105px"><div class="badge"></div><ul>
    <li>Dental Emergencies</li><li>Dental Health</li><li>Dental Insurance</li><li>Kids Corner</li><li>Dental Terminology</li></ul></div>
  <div class="link-col" style="left:200px"><div class="badge"></div><ul>
    <li>Course Outlines</li><li>Upcoming Courses</li><li>Web Links</li><li>Dr. Aldren CV</li><li>Study Store</li></ul></div>
</div>

</body>
</html>
```